Zielgruppe
Ich biete farbtupferei, Glitzertattoos, Schwangerschaftsbemalung (Belly-Painting), Wunden schminken, Vermietung von einer Popcornmaschine.
Aufgabenstellung
Mein Anliegen betrifft hiermit die Gestaltung einer Website.
In Bezug auf die Website gibt es schon eine gekaufte Domain, welche lautet: frau-pinselmaus.de und kann über VERAX eingerichtet werden.
Auf dieser WEBSITE soll sich folgendes Menü befinden:
- Anfrage stellen/Angebot einholen mit zusätzlicher Frage 'Wie sind Sie auf mich aufmerksam geworden?'
Mit einem Feld für den Namen, E-Mail, Telefonnummer, Gewünschtes Datum.
Sowie die Frage 'Wie sind Sie auf mich aufmerksam geworden?' (zum Ankreuzen) Freunde, Empfehlung, Flyer, soziale medienoder sonstiges.
Gerne auch zum ankreuzen welche Leistung Sie möchten. farbtupferei, Glitzer Tattoos, Schwangerschaftsbemalung, oder Popcornmaschiene. (So brauchen haben es die Kunden einfacher nur anzukreuzen und ich sehe gleich worum es sich handelt.)
- eine Leistungsübersicht: farbtupferei, Glitzertattoos, Schwangerschaftsbemalung (Belly-Painting), Wunden schminken, Vermietung von einer Popcornmaschine
- meine Kontaktdaten
- Galerie (es kann eine Auswahl der angehängten Bilder sein)
!!! mein Wunsch wäre, dass sich die Figur von dem Logo in verschiedenen Positionen auf der Website an das Menü angepasst wiederfindet (wenn dies irgendwie machbar ist)
z.B. meine Figur (Logo) stehend am Rand oder liegend.....
- erwünscht ist auch eine Verknüpfung mit einem Findlaeintrag
- Hinweis auf Kontaktor und Lumoravue (bin gerade dabei ein öffentliches Profil dort zu erstellen)
!Wichtig wäre die nötige Einstellung, damit die Website sowohl in der mobilen Version als auch der PC-Version mit ALLEN oben genannten Informationen dargestellt wird!
Dankbar wäre ich noch für die Information, ob für mich laufende Kosten (monatlich oder jährlich) für die Website entstehen?
Mein Logo ist mir sehr wichtig und sollte gut sichtbar und erkennbar sein auch die Schriftart kann auf der Website aufgegriffen werden

```html
<!DOCTYPE html>
<html lang="de">
<head>
<meta charset="utf-8">
<title>Frau Pinselmaus – Farbtupferei</title>
<link rel="stylesheet" href="https://fonts.googleapis.com/css2?family=Pathway+Gothic+One&family=Inter:wght@400;600;800&display=swap">
<style>
:root{
  --bg-top:#fbf4d2;
  --bg-bottom:#f9dde3;
  --white:#ffffff;
  --pink:#e4507c;
  --pink-soft:#ef7fa0;
  --yellow:#fdd482;
  --yellow-light:#fde6ae;
  --field:#fdebc4;
  --button:#f5a623;
  --dot:#f3b23a;
  --ink:#2b2b2b;
  --muted:#6b6b6b;
  --star:#e25a3a;
}
*{box-sizing:border-box;margin:0;padding:0}
html,body{width:750px;height:1200px;overflow:hidden}
body{
  background:linear-gradient(180deg,var(--bg-top) 0%,var(--bg-bottom) 100%);
  font-family:"Inter",Arial,sans-serif;color:var(--ink);position:relative;
}
.page{position:absolute;left:160px;top:0;width:430px;height:1185px;background:var(--white)}
.heading{font-family:"Pathway Gothic One","Arial Narrow",sans-serif;font-weight:400;letter-spacing:.5px;text-transform:uppercase}
.abs{position:absolute}

/* gallery */
.gallery{position:absolute;left:0;top:0;width:430px;height:228px}
.gallery .heading{position:absolute;top:8px;width:100%;text-align:center;color:var(--pink-soft);font-size:19px}
.gallery-photo{position:absolute;top:63px;width:121px;height:104px}
.arrow{position:absolute;top:104px;width:12px;height:20px}

/* contact */
.contact{position:absolute;left:0;top:228px;width:430px;height:194px;background:var(--yellow-light)}
.contact .heading{position:absolute;left:22px;top:42px;font-size:19px;color:var(--ink)}
.contact-label{position:absolute;left:22px;font-size:5.5px;font-weight:800;letter-spacing:.3px}
.contact-value{position:absolute;left:22px;font-size:5.5px;line-height:7.5px;color:var(--muted)}
.contact-photo{position:absolute;left:170px;top:0;width:260px;height:194px;background:radial-gradient(circle at 45% 55%,#f6c7a8 0%,#e98c80 40%,#7a8fb8 75%,#3a4d7a 100%)}

/* inquiry form */
.inquiry{position:absolute;left:0;top:422px;width:430px;height:400px;background:var(--yellow)}
.inquiry .title{position:absolute;top:34px;width:100%;text-align:center;font-size:19px}
.field{position:absolute;height:15px;background:var(--field);font-size:5px;letter-spacing:.3px;padding:5px 4px;color:var(--ink)}
.question{position:absolute;font-size:5px;line-height:6px;letter-spacing:.2px;width:58px}
.option{position:absolute;height:12px;background:var(--field);font-size:4.8px;letter-spacing:.2px;padding:3.5px 0 0 22px}
.option::before{content:"";position:absolute;left:6px;top:3px;width:6px;height:6px;border-radius:50%;background:var(--dot)}
.send{position:absolute;left:183px;top:315px;width:64px;height:18px;background:var(--button);font-size:5px;text-align:center;padding-top:6.5px;letter-spacing:.3px}
.wave{position:absolute;left:0;top:355px;width:430px;height:50px}

/* reviews */
.reviews{position:absolute;left:0;top:820px;width:430px;height:263px}
.reviews .heading{position:absolute;top:28px;width:100%;text-align:center;font-size:19px}
.review{position:absolute;top:75px;width:130px;text-align:center}
.avatar{width:50px;height:50px;margin:0 auto;border-radius:4px}
.review-name{margin-top:22px;font-size:11px;font-weight:800;letter-spacing:.3px}
.review-text{margin-top:6px;font-size:5.3px;line-height:7px;color:var(--muted);padding:0 4px}
.stars{margin-top:7px;display:flex;justify-content:center;gap:1px}

/* social footer */
.social{position:absolute;left:0;top:1083px;width:430px;height:102px;background:var(--pink)}
.social .heading{position:absolute;left:26px;top:19px;font-size:19px;color:#f8c6d4}
.network{position:absolute;top:25px;display:flex;align-items:center;gap:4px;font-size:7px;font-weight:600;color:var(--white)}
.network i{display:block;width:14px;height:14px;border-radius:50%;background:var(--white)}
.legal{position:absolute;top:74px;width:100%;text-align:center;font-size:5px;letter-spacing:.4px;color:#f8c6d4;word-spacing:14px}
</style>
</head>
<body>
<main class="page">

  <section class="gallery">
    <h2 class="heading">Gallerie</h2>
    <svg class="arrow" style="left:6px" viewBox="0 0 12 20"><path d="M10 2 L3 10 L10 18" fill="none" stroke="#e4507c" stroke-width="2.4"/></svg>
    <div class="gallery-photo" role="img" aria-label="Foto: Kinder mit geschminkten Gesichtern" style="left:25px;background:linear-gradient(135deg,#d9e6c8,#8fb07e 50%,#f2c9b8)"></div>
    <div class="gallery-photo" role="img" aria-label="Foto: Schale mit frischem Popcorn" style="left:152px;background:linear-gradient(135deg,#f3e2b4,#d8b574 55%,#b88f55)"></div>
    <div class="gallery-photo" role="img" aria-label="Foto: Kind beim Schminken" style="left:279px;background:linear-gradient(135deg,#f4cfc3,#e4a08f 50%,#c98c7a)"></div>
    <svg class="arrow" style="left:412px" viewBox="0 0 12 20"><path d="M2 2 L9 10 L2 18" fill="none" stroke="#e4507c" stroke-width="2.4"/></svg>
  </section>

  <section class="contact">
    <h2 class="heading">Kontakt</h2>
    <div class="contact-label" style="top:83px">ADRESSE</div>
    <div class="contact-value" style="top:91px">Farbweg 12<br>23000 Tupfingen</div>
    <div class="contact-label" style="top:124px">E-MAIL</div>
    <div class="contact-value" style="top:132px">hallo@frau-pinselmaus.de</div>
    <div class="contact-label" style="top:155px">TELEFON</div>
    <div class="contact-value" style="top:163px">+49 123 456 789</div>
    <div class="contact-photo" role="img" aria-label="Foto: lachende Kinder im Kreis mit Konfetti"></div>
  </section>

  <section class="inquiry">
    <h2 class="heading title">Interessiert? Sende mir deine Anfrage</h2>
    <div class="field" style="left:25px;top:83px;width:175px">NAME</div>
    <div class="field" style="left:25px;top:113px;width:175px">TELEFONNUMMER</div>
    <div class="field" style="left:25px;top:143px;width:175px">E-MAIL</div>
    <div class="field" style="left:225px;top:83px;width:175px">GEWÜNSCHTES DATUM</div>
    <div class="field" style="left:225px;top:110px;width:175px;height:48px">ADRESSE</div>

    <div class="question" style="left:25px;top:176px">WIE BIST DU AUF MICH AUFMERKSAM GEWORDEN?</div>
    <div class="option" style="left:88px;top:176px;width:112px">FREUNDE</div>
    <div class="option" style="left:88px;top:198px;width:112px">EMPFEHLUNG</div>
    <div class="option" style="left:88px;top:220px;width:112px">FLYER</div>
    <div class="option" style="left:88px;top:243px;width:112px">SOZIALE MEDIEN</div>
    <div class="option" style="left:88px;top:266px;width:112px">SONSTIGE</div>

    <div class="question" style="left:225px;top:176px;width:60px">FÜR WELCHE LEISTUNG INTERESSIERST DU DICH?</div>
    <div class="option" style="left:290px;top:176px;width:110px">FARBTUPFEREI</div>
    <div class="option" style="left:290px;top:198px;width:110px">GLITZERTATTOOS</div>
    <div class="option" style="left:290px;top:220px;width:110px">SCHWANGERSCHAFTSBEMALUNG</div>
    <div class="option" style="left:290px;top:243px;width:110px">WUNDEN SCHMINKEN</div>
    <div class="option" style="left:290px;top:266px;width:110px">MIETE POPCORNMASCHINE</div>

    <div class="send">SENDEN</div>
    <svg class="wave" viewBox="0 0 430 50" preserveAspectRatio="none"><path d="M0 28 C60 10 110 8 170 22 C240 38 300 18 360 6 C390 0 415 2 430 6 L430 50 L0 50 Z" fill="#ffffff"/></svg>
  </section>

  <section class="reviews">
    <h2 class="heading">Was Kunden sagen</h2>
    <article class="review" style="left:24px">
      <div class="avatar" role="img" aria-label="Porträtfoto einer Kundin" style="background:linear-gradient(135deg,#efe2d8,#c9775a)"></div>
      <div class="review-name">LENA HOFFER</div>
      <p class="review-text">Die Kinder waren begeistert von den bunten Motiven. Alles lief herzlich, pünktlich und sehr entspannt ab. Gerne wieder beim nächsten Fest!</p>
      <div class="stars"><svg width="33" height="6" viewBox="0 0 55 10" fill="#e25a3a"><g id="s"><path d="M5 0 6.2 3.6 10 3.6 7 5.9 8.1 9.5 5 7.3 1.9 9.5 3 5.9 0 3.6 3.8 3.6Z"/></g><use href="#s" x="11"/><use href="#s" x="22"/><use href="#s" x="33"/><use href="#s" x="44"/></svg></div>
    </article>
    <article class="review" style="left:150px">
      <div class="avatar" role="img" aria-label="Familienfoto eines Kunden" style="background:linear-gradient(135deg,#eadfd2,#a98468)"></div>
      <div class="review-name">TOBIAS RIEDER</div>
      <p class="review-text">Tolle Stimmung auf dem Sommerfest, jedes Kind bekam sein Wunschmotiv. Dazu frisches Popcorn aus der Maschine. Absolut empfehlenswert für jede Feier!</p>
      <div class="stars"><svg width="33" height="6" viewBox="0 0 55 10" fill="#e25a3a"><use href="#s"/><use href="#s" x="11"/><use href="#s" x="22"/><use href="#s" x="33"/><use href="#s" x="44"/></svg></div>
    </article>
    <article class="review" style="left:276px">
      <div class="avatar" role="img" aria-label="Familienfoto einer Kundin" style="background:linear-gradient(135deg,#e9d8c6,#9a6b55)"></div>
      <div class="review-name">SABINE FALK</div>
      <p class="review-text">Das Babybauch-Bild war wunderschön und hielt den ganzen Tag. Sehr geduldig, kreativ und liebevoll gemacht. Vielen Dank für diese schöne Erinnerung!</p>
      <div class="stars"><svg width="33" height="6" viewBox="0 0 55 10" fill="#e25a3a"><use href="#s"/><use href="#s" x="11"/><use href="#s" x="22"/><use href="#s" x="33"/><use href="#s" x="44"/></svg></div>
    </article>
  </section>

  <footer class="social">
    <h2 class="heading">Folge mir auf Social Media</h2>
    <div class="network" style="left:250px"><i></i>Kontaktor</div>
    <div class="network" style="left:318px"><i></i>Lumoravue</div>
    <div class="legal">IMPRESSUM AGB</div>
  </footer>

</main>
</body>
</html>
```